RWT Fittings Ltd Business Cards

We need a business card with our business logo. We provide window and door installations on high-rises in west coast British Colombia, Canada.

I would like my business information and details on one side of the card, and the other side the company name with logo

Target Market(s)

General Contractors

Industry/Entity Type

Construction

Contact Information for Business Card

one side i want my company name and logo in the dark theme logo that i provided

Requirements
Must have
• Marco Peltieri, 16045518293, RWTFittings@mailbox-demo.com, 1407-5194 Linden Row Burnaby BC, V5H 2K9, Owner & Manager

```html
<!DOCTYPE html>
<html lang="en">
<head>
<meta charset="utf-8">
<title>RWT Fittings Ltd – Business Cards</title>
<link rel="stylesheet" href="https://fonts.googleapis.com/css2?family=Open+Sans:wght@400;600;700&display=swap">
<style>
  :root {
    --stage: #3a3a3a;
    --card-white: #ffffff;
    --card-black: #181818;
    --brand-blue: #29a8e0;
    --brand-grey: #9a9a9a;
    --ink-dark: #2a2a2a;
    --ink-light: #f2f2f2;
  }
  * { box-sizing: border-box; margin: 0; padding: 0; }
  html, body { width: 1200px; height: 780px; overflow: hidden; }
  body {
    background: var(--stage);
    font-family: "Open Sans", Arial, sans-serif;
    position: relative;
  }
  .card {
    position: absolute;
    top: 240px;
    width: 525px;
    height: 300px;
    overflow: hidden;
    box-shadow: 0 10px 30px rgba(0,0,0,0.45);
  }
  .card--front { left: 50px; background: var(--card-white); }
  .card--back { left: 625px; background: var(--card-black); }

  .card__wave { position: absolute; inset: 0; width: 100%; height: 100%; }

  .brand {
    position: absolute;
    display: flex;
    align-items: center;
    gap: 10px;
    color: var(--brand-blue);
    font-weight: 600;
    white-space: nowrap;
  }
  .brand__mark { background: var(--brand-blue); flex: none; }
  .card--front .brand { left: 36px; top: 40px; font-size: 28px; }
  .card--front .brand__mark { width: 30px; height: 30px; }

  .holder {
    position: absolute;
    right: 40px;
    top: 126px;
    text-align: right;
  }
  .holder__name { color: var(--brand-blue); font-weight: 700; font-size: 21px; line-height: 1.2; }
  .holder__role { color: var(--ink-dark); font-size: 13px; margin-top: 2px; }
  .edge-stripe {
    position: absolute;
    right: 0; top: 128px;
    width: 14px; height: 56px;
    background: var(--brand-blue);
  }

  .contact {
    position: absolute;
    right: 78px;
    top: 232px;
    color: var(--ink-light);
    font-size: 11px;
    line-height: 14px;
    text-align: right;
  }
  .contact__line { display: flex; justify-content: flex-end; align-items: center; gap: 6px; }
  .contact__icon { width: 11px; height: 11px; flex: none; }
  .contact__spacer { width: 11px; flex: none; }

  .card__pattern {
    position: absolute;
    inset: 0;
    background: radial-gradient(ellipse at 50% 50%, #262626 0%, #1c1c1c 60%, #141414 100%);
  }
  .card--back .brand {
    left: 50%; top: 50%;
    transform: translate(-50%, -50%);
    font-size: 32px;
  }
  .card--back .brand__mark { width: 34px; height: 34px; }
</style>
</head>
<body>

  <section class="card card--front" aria-label="Business card front">
    <svg class="card__wave" viewBox="0 0 525 300" aria-hidden="true">
      <path d="M0,118 C40,185 120,192 250,202 C380,212 470,220 525,262 L525,300 L0,300 Z" fill="var(--card-black)"/>
      <path d="M0,110 C40,178 120,184 250,194 C380,204 470,212 525,254" fill="none" stroke="var(--brand-blue)" stroke-width="4"/>
      <path d="M14,100 C50,160 130,168 255,180 C380,192 470,200 525,240" fill="none" stroke="var(--brand-grey)" stroke-width="5"/>
    </svg>

    <div class="brand">
      <span class="brand__mark"></span>
      <span class="brand__name">RWT Fittings Ltd</span>
    </div>

    <div class="holder">
      <p class="holder__name">Marco Peltieri</p>
      <p class="holder__role">Owner &amp; Manager</p>
    </div>
    <div class="edge-stripe"></div>

    <div class="contact">
      <p class="contact__line">1407-5194 Linden Row<span class="contact__spacer"></span></p>
      <p class="contact__line">Burnaby BC, V5H 2K9<span class="contact__spacer"></span></p>
      <p class="contact__line">16045518293
        <svg class="contact__icon" viewBox="0 0 12 12" aria-hidden="true">
          <path d="M2.5,1 L4.5,1 L5.2,3.4 L4,4.3 C4.6,5.8 6.2,7.4 7.7,8 L8.6,6.8 L11,7.5 L11,9.5 C11,10.4 10.3,11 9.5,11 C5,10.7 1.3,7 1,2.5 C1,1.7 1.6,1 2.5,1 Z" fill="var(--brand-blue)"/>
        </svg>
      </p>
      <p class="contact__line">RWTFittings@mailbox-demo.com
        <svg class="contact__icon" viewBox="0 0 12 12" aria-hidden="true">
          <rect x="0.5" y="2.5" width="11" height="7.5" rx="1" fill="var(--brand-blue)"/>
          <path d="M1,3 L6,7 L11,3" fill="none" stroke="var(--card-black)" stroke-width="1"/>
        </svg>
      </p>
    </div>
  </section>

  <section class="card card--back" aria-label="Business card back">
    <div class="card__pattern" role="img" aria-label="Faint repeating tone-on-tone building pattern across the dark card"></div>
    <div class="brand">
      <span class="brand__mark"></span>
      <span class="brand__name">RWT Fittings Ltd</span>
    </div>
  </section>

</body>
</html>
```